Business Cards Needed for Innovative Healthcare Marketing Company

We are a marketing company focused on healthcare. Our company is all about rebranding yourself renewing your image and generating results. The phoenix stands for "reborn" or "rising" which we provide new brands for our clients we take their old brands and renew it with creativity and innovation. I am looking for a business card with color dimension. I have attached an example of a card I think has the look and feel of what I am trying to accomplish. I like that the card example has black and grey font colors, I like the font placement and the small logo, I really like the use of the colors on the right those are the colors of my logo. My logo is phoenix so maybe incorporating flames similar to that design. I would like the back a solid color maybe red with an opaque version of the logo and website. As a marketing company I am always open to creative liberty!

Target Market(s)

Doctors and business professionals.

Industry/Entity Type

Marketing

Contact Information for Business Card

Valcorne Health Care Marketing
Marla Tenwick- CEO
#(512)638-2974
email-marla@valcorne.com
website- valcorne.com

Font styles to use
Sans Serif

Colors
ec1f27
f37122
ffc214
fbed22
fbf289
f04a50

Requirements
Must have
• The logo and required information
Nice to have
• icons by the information
Should not have
• child like font

```html
<!DOCTYPE html>
<html lang="en">
<head>
<meta charset="utf-8">
<title>Valcorne Health Care Marketing – Business Card</title>
<link rel="stylesheet" href="https://fonts.googleapis.com/css2?family=Open+Sans:wght@300;400;700&display=swap">
<style>
  :root {
    --stage: #2a2624;
    --card: #050505;
    --orange: #f37122;
    --amber: #f7941d;
    --red: #ec1f27;
    --crimson: #c1272d;
    --grey: #c9c9c9;
    --muted: #9a9a9a;
  }
  * { box-sizing: border-box; margin: 0; padding: 0; }
  html, body {
    width: 1200px; height: 844px; overflow: hidden;
    background: var(--stage);
    font-family: "Open Sans", Arial, sans-serif;
  }
  .stage {
    position: relative; width: 1200px; height: 844px;
    display: flex; align-items: center; justify-content: center; gap: 40px;
  }
  .card {
    position: relative; width: 540px; height: 310px;
    background: var(--card); overflow: hidden;
    box-shadow: 0 10px 30px rgba(0,0,0,.5);
  }
  /* Front */
  .card--front .band {
    position: absolute; left: 0; right: 0; height: 14px; background: var(--orange);
  }
  .card--front .band--top { top: 0; }
  .card--front .band--bottom { bottom: 0; }
  .brand-mark {
    position: absolute; left: 40px; top: 0; bottom: 0; width: 200px;
    display: flex; align-items: center; justify-content: center; gap: 10px;
  }
  .brand-mark__dot {
    width: 16px; height: 16px; border-radius: 50%; background: var(--orange); flex: none;
  }
  .brand-mark__name {
    font-weight: 700; font-size: 30px; color: var(--orange); letter-spacing: .5px;
  }
  .details {
    position: absolute; left: 270px; top: 92px;
  }
  .details__name { font-weight: 700; font-size: 19px; color: var(--orange); line-height: 1.1; }
  .details__role { font-size: 13px; color: var(--grey); margin-top: 2px; }
  .contact { list-style: none; margin-top: 18px; }
  .contact__item {
    display: flex; align-items: center; gap: 10px;
    font-size: 14px; color: var(--grey); line-height: 22px;
  }
  .contact__icon { width: 11px; height: 11px; flex: none; }
  /* Back */
  .tab {
    position: absolute; width: 22px; height: 40px;
    background: linear-gradient(180deg, var(--crimson), var(--orange));
  }
  .tab--right { right: 0; top: 26px; }
  .tab--left { left: 0; top: 178px; }
  .wordmark {
    position: absolute; left: 0; right: 0; top: 0; bottom: 0;
    display: flex; align-items: center; justify-content: center; gap: 14px;
  }
  .wordmark__square { width: 14px; height: 14px; background: var(--red); flex: none; }
  .wordmark__text {
    font-weight: 300; color: var(--red); line-height: 1.15;
  }
  .wordmark__name { display: block; font-size: 40px; letter-spacing: 2px; }
  .wordmark__line { display: block; font-size: 12px; letter-spacing: 1.5px; }
</style>
</head>
<body>
<main class="stage">
  <section class="card card--front" aria-label="Business card front">
    <div class="band band--top"></div>
    <div class="brand-mark">
      <span class="brand-mark__dot"></span>
      <span class="brand-mark__name">Valcorne</span>
    </div>
    <div class="details">
      <p class="details__name">Marla Tenwick</p>
      <p class="details__role">CEO</p>
      <ul class="contact">
        <li class="contact__item">
          <svg class="contact__icon" viewBox="0 0 12 12"><path fill="#f37122" d="M2.5 1l2 2.2-1 1.3a7 7 0 0 0 4 4l1.3-1L11 9.5 9.6 11C5 10.6 1.4 7 1 2.4z"/></svg>
          (512)638-2974
        </li>
        <li class="contact__item">
          <svg class="contact__icon" viewBox="0 0 12 12"><rect x="1" y="2.5" width="10" height="7" fill="#f37122"/><path d="M1 2.8l5 3.7 5-3.7" fill="none" stroke="#050505" stroke-width="1"/></svg>
          marla@valcorne.com
        </li>
        <li class="contact__item">
          <svg class="contact__icon" viewBox="0 0 12 12"><circle cx="6" cy="6" r="5" fill="#f37122"/><path d="M1 6h10M6 1c-2.5 3-2.5 7 0 10M6 1c2.5 3 2.5 7 0 10" fill="none" stroke="#050505" stroke-width=".8"/></svg>
          www.valcorne.com
        </li>
      </ul>
    </div>
    <div class="band band--bottom"></div>
  </section>

  <section class="card card--back" aria-label="Business card back">
    <div class="tab tab--right"></div>
    <div class="tab tab--left"></div>
    <div class="wordmark">
      <span class="wordmark__square"></span>
      <p class="wordmark__text">
        <span class="wordmark__name">VALCORNE</span>
        <span class="wordmark__line">HEALTH CARE MARKETING</span>
      </p>
    </div>
  </section>
</main>
</body>
</html>
```